Waste management company seeks a new website design

We need a website design for an environmental services company called 'Laanemetsa Haldusgrupp.' We manage waste collection and recycling for 100K+ households and businesses across Estonia. Please use logos and colors from attached CVI file. The design should be extensively usable for our self-service portal and have a mobile-first approach as it will be turned into an app in the future. The new website should highlight our commitment to sustainability and provide easy access to our services with a clean, modern design. UX inspiration from https://ruvako.eu/et-ee/

```html
<!DOCTYPE html>
<html lang="et">
<head>
<meta charset="utf-8">
<title>Laanemetsa Haldusgrupp – veebilehe kujundus</title>
<link href="https://fonts.googleapis.com/css2?family=Montserrat:wght@300;400;500;600;700&display=swap" rel="stylesheet">
<style>
:root{
  --board:#3a3531;
  --lime:#d3df2c;
  --label:#c9d12f;
  --taupe:#7d7169;
  --taupe-light:#b9b0aa;
  --ink:#5c5550;
  --muted:#7a726c;
  --soft:#f3f3f2;
  --white:#ffffff;
}
*{margin:0;padding:0;box-sizing:border-box}
html,body{width:1200px;height:1200px;overflow:hidden;background:var(--board)}
body{font-family:'Montserrat',sans-serif;color:var(--ink)}
.stage{position:absolute;left:0;top:0;width:1932px;height:1932px;transform:scale(.62112);transform-origin:0 0}
.a{position:absolute}
.view-label{color:var(--label);font-weight:300;font-size:20px;line-height:23px;text-align:center}
.frame{position:absolute;top:0;height:1932px;overflow:hidden;background:var(--white)}
.frame-mobile{left:531px;width:371px}
.frame-desktop{left:1115px;width:499px}
.section{position:absolute;left:0;width:100%;overflow:hidden}
.center{left:0;width:100%;text-align:center}
.logo-dot{position:absolute;border-radius:50%;background:var(--taupe)}
.logo-name{position:absolute;font-weight:600;color:#6a625c}
.hero{background:var(--taupe)}
.leaf{position:absolute;background:var(--lime);border-radius:50%}
.hero-photo{position:absolute;border-radius:50%;background:radial-gradient(circle at 45% 40%,#e4c7a4 0%,#b9a08a 35%,#8f8478 70%,#d9c9b4 100%)}
.hero-title{position:absolute;color:var(--lime);font-weight:500;letter-spacing:-.3px}
.hero-text{position:absolute;color:var(--white)}
.btn{position:absolute;background:var(--lime);color:#4c4a2a;display:flex;align-items:center;justify-content:center;font-weight:500}
.h2{position:absolute;font-weight:600;color:var(--ink)}
.body-text{position:absolute;color:var(--ink)}
.photo{position:absolute}
.ph-bins{background:linear-gradient(160deg,#8fae5c,#3f5a3a 55%,#c6c4b0)}
.ph-child{background:linear-gradient(160deg,#6c7a4a,#c79a62 50%,#8a6b45)}
.ph-grass{background:linear-gradient(170deg,#e9c77b,#9d7a3a 50%,#3d3522)}
.ph-bag{background:linear-gradient(170deg,#b89a78,#d9d2c6 55%,#a7a196)}
.ph-hiker{background:linear-gradient(165deg,#d7a86a,#8a6a4c 45%,#c9c1b4 75%,#5c4a3a)}
.ph-woman{background:linear-gradient(165deg,#e0b878,#9d7a5a 60%,#5e4a3c)}
.ph-pines{background:linear-gradient(180deg,#d8cfc0,#a79a86 60%,#6e6553)}
.ph-flowers{background:linear-gradient(160deg,#cdd0a0,#7e9a4a 50%,#3e5c8a)}
.ph-smile{background:linear-gradient(160deg,#5e4a32,#e2bc86 50%,#4a3b2c)}
.ph-gloves{background:linear-gradient(180deg,#8fc2de,#b9d6e6 55%,#d49a52)}
.ph-forest{background:linear-gradient(180deg,#4f5a3a,#7fa050 55%,#b9d27a)}
.ph-snow{background:linear-gradient(180deg,#c9d2da,#e9eef2 50%,#8b94a0)}
.ph-field{background:linear-gradient(120deg,#6b5430,#d6a452 45%,#f3d48c 70%,#8c7a5a)}
.caption{position:absolute;font-size:4.6px;text-transform:uppercase;color:var(--muted);text-align:center}
.kicker{position:absolute;color:var(--lime);font-size:6.5px;text-transform:uppercase;letter-spacing:.3px}
.stat-num{position:absolute;color:var(--lime);font-weight:700}
.stat-text{position:absolute;color:var(--muted);font-weight:300}
.nav-link{position:absolute;top:17px;font-size:6px;color:var(--taupe);font-weight:500}
.field{position:absolute;background:var(--white);border:1px solid #ddd;font-size:4.5px;color:#999;padding-left:5px;display:flex;align-items:center}
.foot-head{position:absolute;font-size:7px;color:var(--taupe);font-weight:500}
.foot-item{position:absolute;font-size:5px;color:var(--taupe);line-height:11px}
.social{position:absolute;width:9px;height:9px;border-radius:50%;background:#9a8f86}
</style>
</head>
<body>
<div class="stage">

  <div class="a view-label" style="left:395px;top:48px;width:120px">Mobile View</div>
  <div class="a view-label" style="left:1020px;top:48px;width:100px">Desktop<br>View</div>

  <!-- MOBILE -->
  <div class="frame frame-mobile">
    <header class="section" style="top:3px;height:49px;background:var(--soft)">
      <div class="logo-dot" style="left:31px;top:14px;width:22px;height:22px"></div>
      <div class="logo-name" style="left:66px;top:15px;font-size:10.5px;line-height:11.5px">Laanemetsa<br>Haldusgrupp</div>
      <div class="a" style="left:309px;top:25px;width:15px;height:1px;background:#777"></div>
      <div class="a" style="left:309px;top:28px;width:15px;height:1px;background:#777"></div>
      <div class="a" style="left:309px;top:31px;width:15px;height:1px;background:#777"></div>
    </header>

    <section class="section hero" style="top:52px;height:266px">
      <div class="hero-photo" role="img" aria-label="Naine järve ääres päikesevalguses" style="left:118px;top:73px;width:330px;height:330px"></div>
      <div class="leaf" role="img" aria-label="Dekoratiivne leheillustratsioon" style="left:192px;top:-40px;width:200px;height:120px;transform:rotate(-15deg)"></div>
      <h1 class="hero-title" style="left:22px;top:48px;width:130px;font-size:13.5px;line-height:16px">Hoolime loodusest, hoolime tulevikust</h1>
      <p class="hero-text" style="left:22px;top:88px;width:115px;font-size:7.2px;line-height:11.8px">Laanemetsa Haldusgrupp on Eesti juhtiv jäätmekäitlus- ja kommunaalteenuseid pakkuv kontsern, mille põhitegevuseks on olmejäätmete kogumine</p>
      <div class="btn" style="left:22px;top:172px;width:64px;height:18px;font-size:6.2px">LISATEAVE</div>
    </section>

    <section class="section" style="top:318px;height:522px">
      <h2 class="h2 center" style="top:23px;font-size:11.5px">Meist</h2>
      <p class="body-text center" style="top:45px;font-size:7.5px;line-height:12px;padding:0 2px">Laanemetsa Haldusgrupp on Eesti juhtiv jäätmekäitlus- ja kommunaalteenuseid<br>pakkuv kontsern, mille põhitegevuseks on olmejäätmete<br>kogumine. Lisaks sellele tegeleb ettevõte teisese toorme, ehitusjäätmete<br>ning muude jäätmete kogumisega.</p>
      <h2 class="h2" style="left:0;width:371px;text-align:center;top:136px;font-size:10.5px;padding-left:16px">Teenused Pakkumised</h2>
      <div class="photo ph-bins" role="img" aria-label="Jäätmekonteinerid rivis" style="left:52px;top:163px;width:101px;height:117px"></div>
      <div class="caption" style="left:52px;top:284px;width:101px">Jäätmete kogumine</div>
      <div class="photo ph-child" role="img" aria-label="Laps hoiab taaskasutuskasti" style="left:184px;top:163px;width:101px;height:117px"></div>
      <div class="caption" style="left:184px;top:284px;width:101px">Ringlussevõtt</div>
      <div class="photo ph-grass" role="img" aria-label="Käsi puudutab kõrrelist loojangus" style="left:54px;top:310px;width:101px;height:117px"></div>
      <div class="caption" style="left:54px;top:432px;width:112px">Hooldusteenust</div>
      <div class="photo ph-bag" role="img" aria-label="Ehitusjäätmete kott" style="left:184px;top:310px;width:101px;height:117px"></div>
      <div class="caption" style="left:184px;top:432px;width:101px">Ehitusjäätmed</div>
      <div class="btn" style="left:133px;top:458px;width:64px;height:18px;font-size:6.2px">LISATEAVE</div>
    </section>

    <section class="section" style="top:840px;height:374px;background:var(--soft)">
      <div class="kicker" style="left:0;width:371px;text-align:center;top:18px;padding-left:25px">Miks meie</div>
      <h2 class="body-text" style="left:70px;width:250px;text-align:center;top:36px;font-size:9.5px;line-height:12px;font-weight:400">Haldame Jäätmete kogumist ja taaskasutust 100 000+ majapidamisele ja ettevõttele üle Eesti.</h2>
      <p class="body-text" style="left:68px;width:240px;text-align:center;top:88px;font-size:5.4px;line-height:10px;color:var(--muted)">Ettevõttes on juurutatud integreeritud töötervishoiu, tööohutuse-<br>kvaliteedi- ja keskkonnajuhtimise süsteem<br>ISO 9001, ISO 14001 ja ISO 45001 standardite põhjal.<br>Nimetatud standardite järgimine eeldab pidevat arengut nii tööohutuse- ja<br>-tervishoiu kui kvaliteedi- ja keskkonnaalastes aspektides. Laanemetsa<br>Haldusgrupp pakub oma teenuseid suuremates<br>Eesti keskustes ja nende ümbruses</p>
      <div class="photo ph-hiker" role="img" aria-label="Vanem naine matkamas sügismetsas" style="left:64px;top:168px;width:248px;height:191px"></div>
    </section>

    <section class="section" style="top:1214px;height:166px">
      <h2 class="h2" style="left:0;width:371px;text-align:center;padding-left:35px;top:30px;font-size:9.5px">Ettevõte Teenindab</h2>
      <div class="stat-num" style="left:19px;top:70px;font-size:11px">+100 000</div>
      <div class="stat-text" style="left:19px;top:84px;font-size:8.5px;line-height:11px">Eestis klienti</div>
      <div class="stat-num" style="left:155px;top:70px;font-size:11px">+250 000</div>
      <div class="stat-text" style="left:150px;top:84px;width:64px;text-align:center;font-size:8.5px;line-height:11px">käitleb üle<br>tonni jäätmeid</div>
      <div class="stat-num" style="left:291px;top:70px;font-size:11px">+600</div>
      <div class="stat-text" style="left:280px;top:82px;width:64px;text-align:center;font-size:8.5px;line-height:11px">Annab tööd<br>ligi inimesele</div>
    </section>

    <section class="section" style="top:1380px;height:420px;background:var(--taupe-light)">
      <h2 class="body-text" style="left:100px;width:150px;text-align:center;top:18px;font-size:6.5px;line-height:8.5px;font-weight:600;color:#4e4743">OLEME SIIN SELLEKS, ET TEID INSPIREERIDA JA VOLITADA</h2>
      <p class="body-text" style="left:90px;width:170px;text-align:center;top:42px;font-size:7.5px;line-height:11.7px;color:#6e6560">Standardite järgimine eeldab pidevat arengut nii tööohutuse- ja -tervishoiu kui kvaliteedi- ja keskkonnaalaste aspektides. Laanemetsa Haldusgrupp pakub oma teenuseid suuremates Eesti keskustes ja nende ümbruses</p>
      <div class="photo ph-woman" role="img" aria-label="Naine mütsiga päikese käes" style="left:38px;top:135px;width:141px;height:117px"></div>
      <div class="photo ph-pines" role="img" aria-label="Udune raba mändidega" style="left:182px;top:135px;width:141px;height:117px"></div>
      <div class="photo ph-flowers" role="img" aria-label="Käed ulatavad metslillede kimpu" style="left:38px;top:255px;width:141px;height:117px"></div>
      <div class="photo ph-smile" role="img" aria-label="Naerev laps" style="left:182px;top:255px;width:141px;height:117px"></div>
      <div class="btn" style="left:115px;top:385px;width:130px;height:25px;font-size:7.3px;font-weight:400">Võtke meiega kohe ühendust</div>
    </section>
  </div>

  <!-- DESKTOP -->
  <div class="frame frame-desktop">
    <nav class="section" style="top:3px;height:32px;background:var(--white)">
      <div class="logo-dot" style="left:22px;top:5px;width:18px;height:18px"></div>
      <div class="logo-name" style="left:56px;top:6px;font-size:9px;line-height:10px">Laanemetsa<br>Haldusgrupp</div>
      <span class="nav-link" style="left:241px;top:14px">Kodu</span>
      <span class="nav-link" style="left:274px;top:14px">Teenindus</span>
      <span class="nav-link" style="left:329px;top:14px">Umbes</span>
      <span class="nav-link" style="left:368px;top:14px">Võta meiega ühendust</span>
      <svg class="a" style="left:465px;top:14px" width="8" height="8" viewBox="0 0 8 8"><circle cx="3.3" cy="3.3" r="2.5" fill="none" stroke="#555" stroke-width="1"/><line x1="5.2" y1="5.2" x2="7.5" y2="7.5" stroke="#555" stroke-width="1"/></svg>
    </nav>

    <section class="section hero" style="top:35px;height:250px">
      <div class="hero-photo" role="img" aria-label="Naine järve ääres päikesevalguses" style="left:265px;top:85px;width:290px;height:290px"></div>
      <div class="leaf" role="img" aria-label="Dekoratiivne leheillustratsioon" style="left:300px;top:-45px;width:220px;height:125px;transform:rotate(-12deg)"></div>
      <h1 class="hero-title" style="left:38px;top:57px;width:200px;font-size:20px;line-height:27px">Hoolime loodusest, hoolime tulevikust</h1>
      <p class="hero-text" style="left:40px;top:117px;width:165px;font-size:6.8px;line-height:9px">Laanemetsa Haldusgrupp on Eesti juhtiv jäätmekäitlus- ja kommunaalteenuseid pakkuv kontsern, mille põhitegevuseks on olmejäätmete kogumine</p>
      <div class="btn" style="left:41px;top:169px;width:61px;height:17px;font-size:5.6px">LISATEAVE</div>
    </section>

    <section class="section" style="top:285px;height:353px">
      <h2 class="h2 center" style="top:20px;font-size:10px">Meist</h2>
      <p class="body-text center" style="top:40px;font-size:6.8px;line-height:11.3px">Laanemetsa Haldusgrupp on Eesti juhtiv jäätmekäitlus- ja kommunaalteenuseid<br>pakkuv kontsern, mille põhitegevuseks on olmejäätmete<br>kogumine. Lisaks sellele tegeleb ettevõte teisese toorme, ehitusjäätmete<br>ning muude jäätmete kogumisega.</p>
      <h2 class="h2" style="left:0;width:499px;text-align:center;padding-left:24px;top:127px;font-size:10px">Teenused Pakkumised</h2>
      <div class="photo ph-bins" role="img" aria-label="Jäätmekonteinerid rivis" style="left:43px;top:151px;width:95px;height:111px"></div>
      <div class="caption" style="left:43px;top:266px;width:95px;font-size:4px">Jäätmete kogumine</div>
      <div class="photo ph-child" role="img" aria-label="Laps hoiab taaskasutuskasti" style="left:149px;top:151px;width:95px;height:111px"></div>
      <div class="caption" style="left:149px;top:266px;width:95px;font-size:4px">Ringlussevõtt</div>
      <div class="photo ph-grass" role="img" aria-label="Käsi puudutab kõrrelist loojangus" style="left:259px;top:151px;width:95px;height:111px"></div>
      <div class="caption" style="left:259px;top:266px;width:105px;font-size:4px">Hooldusteenust</div>
      <div class="photo ph-bag" role="img" aria-label="Ehitusjäätmete kott" style="left:367px;top:151px;width:95px;height:111px"></div>
      <div class="caption" style="left:367px;top:266px;width:95px;font-size:4px">Ehitusjäätmed</div>
      <div class="btn" style="left:219px;top:291px;width:66px;height:18px;font-size:5.6px">LISATEAVE</div>
    </section>

    <section class="section" style="top:638px;height:203px;background:var(--soft);width:497px">
      <div class="photo ph-hiker" role="img" aria-label="Vanem naine matkamas sügismetsas" style="left:11px;top:10px;width:235px;height:182px"></div>
      <div class="kicker" style="left:261px;width:220px;text-align:center;top:25px;font-size:5.5px">Miks meie</div>
      <h2 class="body-text" style="left:266px;width:210px;text-align:center;top:38px;font-size:8.6px;line-height:11px;font-weight:400">Haldame Jäätmete kogumist ja taaskasutust 100 000+ majapidamisele ja ettevõttele üle Eesti.</h2>
      <p class="body-text" style="left:261px;width:220px;text-align:center;top:82px;font-size:5px;line-height:9.4px;color:var(--muted)">Ettevõttes on juurutatud integreeritud töötervishoiu, tööohutuse-<br>kvaliteedi- ja keskkonnajuhtimise süsteem<br>ISO 9001, ISO 14001 ja ISO 45001 standardite põhjal.<br>Nimetatud standardite järgimine eeldab pidevat arengut nii tööohutuse- ja<br>-tervishoiu kui kvaliteedi- ja keskkonnaalastes aspektides. Laanemetsa<br>Haldusgrupp pakub oma teenuseid suuremates<br>Eesti keskustes ja nende ümbruses</p>
      <div class="btn" style="left:335px;top:161px;width:73px;height:18px;font-size:5.6px">LISATEAVE</div>
    </section>

    <section class="section" style="top:841px;height:199px">
      <h2 class="h2" style="left:0;width:499px;text-align:center;top:30px;font-size:8.5px">Ettevõte Teenindab</h2>
      <div class="stat-num" style="left:85px;top:67px;font-size:10px">+100 000</div>
      <div class="stat-text" style="left:85px;top:79px;font-size:8px;line-height:11px">Eestis klienti</div>
      <div class="stat-num" style="left:213px;top:67px;font-size:10px">+250 000</div>
      <div class="stat-text" style="left:208px;top:80px;width:62px;text-align:center;font-size:8px;line-height:11px">käitleb üle<br>tonni jäätmeid</div>
      <div class="stat-num" style="left:342px;top:67px;font-size:10px">+600</div>
      <div class="stat-text" style="left:334px;top:78px;width:60px;text-align:center;font-size:8px;line-height:11px">Annab tööd<br>ligi inimesele</div>
    </section>

    <section class="section" style="top:1040px;height:244px;background:var(--taupe-light)">
      <h2 class="body-text" style="left:30px;width:155px;text-align:center;top:57px;font-size:6px;line-height:8px;font-weight:600;color:#4e4743">OLEME SIIN SELLEKS, ET TEID INSPIREERIDA JA VOLITADA</h2>
      <p class="body-text" style="left:28px;width:160px;text-align:center;top:90px;font-size:7px;line-height:11.2px;color:#6e6560">Standardite järgimine eeldab pidevat arengut nii tööohutuse- ja -tervishoiu kui kvaliteedi- ja keskkonnaalaste aspektides. Laanemetsa Haldusgrupp pakub oma teenuseid suuremates Eesti keskustes ja nende ümbruses</p>
      <div class="btn" style="left:46px;top:185px;width:122px;height:24px;font-size:6.8px;font-weight:400">Võtke meiega kohe ühendust</div>
      <div class="photo ph-woman" role="img" aria-label="Naine mütsiga päikese käes" style="left:211px;top:3px;width:141px;height:117px"></div>
      <div class="photo ph-pines" role="img" aria-label="Udune raba mändidega" style="left:355px;top:3px;width:142px;height:117px"></div>
      <div class="photo ph-flowers" role="img" aria-label="Käed ulatavad metslillede kimpu" style="left:211px;top:123px;width:141px;height:117px"></div>
      <div class="photo ph-smile" role="img" aria-label="Naerev laps" style="left:355px;top:123px;width:142px;height:117px"></div>
    </section>

    <section class="section" style="top:1284px;height:329px">
      <h2 class="h2" style="left:0;width:499px;text-align:center;top:62px;font-size:10px;padding-left:4px">Uudised ja lood</h2>
      <div class="photo ph-gloves" role="img" aria-label="Kindais käed sorteerivad plastpudeleid" style="left:60px;top:100px;width:93px;height:115px"></div>
      <p class="body-text" style="left:62px;top:219px;width:100px;font-size:7px;line-height:9px">Eesti jaoks on jäätmete taaskasutamise trahv silmapiiril, kui edusamme ei toimu</p>
      <div class="body-text" style="left:62px;top:257px;font-size:4px">4-minutine lugemine • 25.6.2024</div>
      <div class="photo ph-forest" role="img" aria-label="Vabatahtlikud koristavad metsa" style="left:196px;top:100px;width:93px;height:115px"></div>
      <p class="body-text" style="left:197px;top:219px;width:100px;font-size:7px;line-height:9px">Eesti jaoks on jäätmete taaskasutamise trahv silmapiiril, kui edusamme ei toimu</p>
      <div class="body-text" style="left:197px;top:257px;font-size:4px">4-minutine lugemine • 25.6.2024</div>
      <div class="photo ph-snow" role="img" aria-label="Prügiauto lumisel tänaval" style="left:338px;top:100px;width:93px;height:115px"></div>
      <p class="body-text" style="left:339px;top:218px;width:100px;font-size:7px;line-height:9px">Eesti jaoks on jäätmete taaskasutamise trahv silmapiiril, kui edusamme ei toimu</p>
      <div class="body-text" style="left:339px;top:256px;font-size:4px">4-minutine lugemine • 25.6.2024</div>
    </section>

    <section class="section ph-field" role="img" aria-label="Käsi puudutab põllukõrsi loojangu valguses" style="top:1613px;height:182px">
      <p class="body-text" style="left:267px;width:180px;text-align:center;top:61px;font-size:7.2px;line-height:9px;color:#3e3a36">Registreeruge, et saada värskendusi meie teenuste ja juhendite kohta ning säästa oma esimesest tellimusest 10%.</p>
      <div class="field" style="left:294px;top:99px;width:131px;height:15px">E-posti aadress</div>
      <div class="btn" style="left:294px;top:118px;width:131px;height:15px;font-size:5px;font-weight:400">ESITA</div>
    </section>

    <footer class="section" style="top:1795px;height:137px;background:#f6f6f5">
      <div class="logo-dot" style="left:37px;top:39px;width:14px;height:14px"></div>
      <div class="logo-name" style="left:57px;top:40px;font-size:5.7px;line-height:6.5px">Laanemetsa<br>Haldusgrupp</div>
      <div class="body-text" style="left:57px;top:55px;font-size:5px;color:var(--taupe)">© 2024</div>
      <div class="foot-head" style="left:180px;top:36px">Ettevõte</div>
      <div class="foot-item" style="left:180px;top:47px">Meist<br>Töövõimalused<br>Meedia<br>Blogi<br>Koubamärgi suunised</div>
      <div class="foot-head" style="left:284px;top:36px">Meie Teenus</div>
      <div class="foot-item" style="left:284px;top:47px">Jäätmekäitluse<br>Taaskasutus<br>Puhastamine<br>Ehituse juhtimine</div>
      <div class="foot-head" style="left:368px;top:36px">Võta meiega ühendust</div>
      <div class="foot-item" style="left:368px;top:47px">Email<br>Phone<br>Social Media</div>
      <div class="social" style="left:369px;top:89px"></div>
      <div class="social" style="left:388px;top:89px"></div>
      <div class="social" style="left:407px;top:89px"></div>
      <div class="social" style="left:426px;top:89px"></div>
    </footer>
  </div>

</div>
</body>
</html>
```